Norrell Advisory WA Business Card

Create an interesting, eye catching and colourful two sided business card. We are a business consulting operation assisting SME's improve all areas of their business. We provide consulting services to assist SME's to create a culture of continuous improvement, making a positive difference in the business. Our tag line is Small changes, big rewards. We want to create a well recognised, innovative brand that can be continued throughout our website, social media and email correspondence.

Target Market(s)

Small to Medium Enterprise Business Owners

Industry/Entity Type

Business Consultant

Contact Information for Business Card

Name of Business: Norrell Advisory - Small Changes Big Rewards
Derek Holloway Ph 0407385510 Megan Holloway Ph 0407913847
Email norrelladvisorywa@mailbox-example.com
Web address TBA
FaceBook page TBA

BACKSIDE OF CARD

Providing assistance with:

• Organisation & Efficiency
• Revenue generation & Marketing
• Financial Management
• Production quality & delivery
• Systems & Process documentation
• Exit Strategy

Font styles to use
Other font styles liked:
• Calibri

Colors

Designer to choose colors to be used in the design.

Requirements
Must have
• Calibri font

```html
<!DOCTYPE html>
<html lang="en">
<head>
<meta charset="utf-8">
<title>Norrell Advisory WA Business Card</title>
<link rel="stylesheet" href="https://fonts.googleapis.com/css2?family=Carlito:wght@400;700&family=Cinzel:wght@500&display=swap">
<style>
  :root {
    --backdrop: #2b2b2d;
    --card: #141414;
    --ink: #ececec;
    --muted: #9a9a9a;
    --gold: #f5b335;
    --yellow: #f7b52c;
    --blue: #1b8fd2;
    --red: #ef4a32;
    --green: #7dbb42;
    --rule: #555;
  }
  * { box-sizing: border-box; margin: 0; padding: 0; }
  html, body { width: 1200px; height: 900px; overflow: hidden; }
  body {
    background: var(--backdrop);
    font-family: "Carlito", "Calibri", sans-serif;
    color: var(--ink);
    position: relative;
  }
  .card {
    position: absolute;
    left: 300px;
    width: 600px;
    height: 340px;
    background: var(--card);
    box-shadow: 0 10px 24px rgba(0,0,0,.55);
    overflow: hidden;
  }
  .card--front { top: 70px; }
  .card--back { top: 470px; }
  .colour-band {
    position: absolute; left: 0; right: 0; bottom: 0; height: 9px;
    display: flex;
  }
  .colour-band span { flex: 1; }
  .colour-band .yellow { background: var(--yellow); }
  .colour-band .blue { background: var(--blue); }
  .colour-band .red { background: var(--red); }
  .colour-band .green { background: var(--green); }

  /* front */
  .brand {
    position: absolute; top: 70px; left: 0; right: 0;
    text-align: center;
  }
  .brand-mark {
    width: 58px; height: 58px; margin: 0 auto 14px;
    background: var(--yellow);
  }
  .brand-name {
    font-family: "Cinzel", serif;
    font-weight: 500;
    font-size: 30px;
    letter-spacing: 1px;
    color: var(--ink);
  }
  .brand-tagline {
    font-size: 13px; letter-spacing: 4px;
    text-transform: uppercase; color: var(--muted);
    margin-top: 2px;
  }
  .contact {
    position: absolute; left: 30px; right: 30px; top: 222px;
    border-top: 1px solid var(--rule);
    padding-top: 14px;
    text-align: center;
    font-size: 14px; line-height: 1.6;
    white-space: nowrap;
  }
  .contact .label { color: var(--blue); font-weight: 700; }
  .contact .sep { color: var(--muted); margin: 0 6px; }

  /* back */
  .partners {
    position: absolute; top: 48px; left: 0; right: 0;
    display: flex; justify-content: center; align-items: flex-start;
  }
  .partner { padding: 0 26px; }
  .partner-name {
    font-family: "Cinzel", serif; font-weight: 500;
    font-size: 25px; color: var(--gold); white-space: nowrap;
  }
  .partner-phone { font-size: 16px; letter-spacing: 1px; }
  .partner--left { text-align: right; }
  .partner-divider { width: 1px; height: 58px; background: var(--rule); margin-top: 14px; }
  .services-heading {
    position: absolute; top: 150px; left: 40px; right: 40px;
    display: flex; align-items: center; gap: 10px;
    color: var(--red); font-weight: 700; font-size: 16px; letter-spacing: 1px;
    text-transform: uppercase; white-space: nowrap;
  }
  .services-heading::before, .services-heading::after {
    content: ""; flex: 1; height: 1px; background: var(--rule);
  }
  .services {
    position: absolute; top: 184px; left: 0; right: 0;
    list-style: none; text-align: center;
    font-size: 17px; line-height: 1.5;
  }
  .services .dot { margin: 0 6px; font-weight: 700; }
  .dot--yellow { color: var(--yellow); }
  .dot--green { color: var(--green); }
</style>
</head>
<body>

<section class="card card--front" aria-label="Business card front">
  <div class="brand">
    <div class="brand-mark"></div>
    <div class="brand-name">Norrell Advisory</div>
    <div class="brand-tagline">Steady steps • lasting gains</div>
  </div>
  <div class="contact">
    <div><span class="label">E:</span> norrelladvisorywa@mailbox-example.com<span class="sep">|</span><span class="label">W:</span> www.norrelladvisory.example</div>
    <div><span class="label">social.example/</span>norrelladvisory</div>
  </div>
  <div class="colour-band"><span class="yellow"></span><span class="blue"></span><span class="red"></span><span class="green"></span></div>
</section>

<section class="card card--back" aria-label="Business card back">
  <div class="partners">
    <div class="partner partner--left">
      <div class="partner-name">Derek Holloway</div>
      <div class="partner-phone">0407385510</div>
    </div>
    <div class="partner-divider"></div>
    <div class="partner partner--right">
      <div class="partner-name">Megan Holloway</div>
      <div class="partner-phone">0407913847</div>
    </div>
  </div>
  <div class="services-heading">Providing assistance with</div>
  <ul class="services">
    <li>Organisation &amp; Efficiency<span class="dot dot--yellow">•</span>Revenue generation &amp; Marketing</li>
    <li>Financial Management<span class="dot dot--yellow">•</span>Production quality &amp; delivery</li>
    <li>Systems &amp; Process documentation<span class="dot dot--green">•</span>Exit Strategy</li>
  </ul>
  <div class="colour-band"><span class="yellow"></span><span class="blue"></span><span class="red"></span><span class="green"></span></div>
</section>

</body>
</html>
```